Systems and Technology Consultants - Website

Design & Build a website for a new company which operates in the Systems and Technology space for Transportation, Government and Commercial sectors.

Overall design should be minimalist in nature.
Should also have a feed that provides news and event updates on the main page.
Logo has already been awarded and should be incorporated into the site.

We like the overall layout, functionality and simplicity of the below sites. Submitted designs could be similar to or a combination of the aspects on these sites, or perhaps a whole different concept - we are open to new ideas.
Norvique.com
Teblo.it

Update 1 Dated 27 May 2014

All I am moving away from the Teblo.it website and would like it to be more aligned with Norvique.com not only in layout but in functionality. I will be extending the deadline of this design brief for two weeks to incorporate additional requirements and will add addtional funding to the project.

Apologies for not having more information available to provide but with so many submissions its getting confusing.

Thanks Derek

Please note that the brief has been updated and the deadline has been extended.

Important: We will need two language versions of the website, English and Arabic; the website is hosted on HostPelican

Hello All, Thank you for your submissions. We have narrowed it down to the final 6 designers and I just wanted to take a moment and provide a bit of feedback regarding the concepts that we like and the modifications we are looking for. First, let me mention some of the design functions we like. - At the top of the homepage we really like the "region" or "language" tab so that the website can be viewed in both English and Arabic. - We like the homepage to have clear color variation so that the different sections of the homepage are distinct. Additionally, we like the bottom portion of the homepage to be in red. We feel that draws attention to our contact information. Again, we would like the colors to integrate black, gray-scale, red, etc. - Having a search tab at the top of the home page, or integrated into the main image, so that the site is easy to navigate. - We especially like the main image to have the scrolling tabs at the bottom so it is easy to browse the services offered (Consultancy, Solutions Architecture, Masters Systems Integration, Independent Design Review). - In regards to the services offered tab we really like the idea that a few people presented that have the outside of our logo with an icon in the middle of consultancy, solutions, etc., etc. Secondly, as mentioned in our brief we really enjoy the design of norvique site. Specially, we enjoy the strong iconic images they use, the way the tabs at the top scroll easily, and contact us page that generates an email. Lastly, I've included some photos of the concept we have been working on. What we are trying to demonstrate is how our company offers a range of services that are essentially linked together. We provide individual services that when combined present the full service package. We would like this concept to be integrated into the over concept of our website. Please feel free to ask for clarification of any of the above points or contact us if you have any additional questions. We appreciate all of your hard work and are very excited to see the updated designs. Best, Marta Vennick Quelbrant Senior Program Manager marta.vennick@quelbrant-example.com

Industry/Entity Type

Government

Font styles to use
Serif
Sans Serif

Requirements
Must have
• Must work on/adapt to various/mobile devices (responsive)
Must be simple and straightforward
Colors should be in line/matching with logo
2 language versions: English and Arabic (no Thai)
Services should be the first group/row of items after/below the main image
Note: the website will be hosted by hostpelican
Nice to have
• Submit feedback form
What's New section
The banner at the bottom of the site should not be too large; we would like a narrow one more
It would be nice if the header/top banner (with Home, About, etc. tabs) could stay in place as you scroll down (like Norvique and Chatterloop)
We will likely only use one image with a Company slogan on the Home page rather than a carousel of images to rotate through
Should not have
• This is the existing website: http://www.quelbrant-example.org
We do not like the animation, the way the banner icons/titles bounce
Not simple enough, we don't like the functionality or how pages load so slowly
We do not like the logo centered - it should be at the left
The banner and its tabs should not be towards the right, we would like them to be centered, to go all the way across and to be below the logo

```html
<!DOCTYPE html>
<html lang="en">
<head>
<meta charset="utf-8">
<title>Quelbrant International</title>
<link rel="stylesheet" href="https://fonts.googleapis.com/css2?family=Roboto:wght@400;500;700&display=swap">
<style>
:root{
  --red:#d6202a;
  --red-dark:#b3161f;
  --ink:#3c3c3c;
  --muted:#8a8a8a;
  --light:#f5f5f5;
  --panel:#e9e9e9;
  --rule:#cfcfcf;
  --footer:#555555;
  --white:#ffffff;
}
*{box-sizing:border-box;margin:0;padding:0}
html,body{width:960px;height:1200px;overflow:hidden}
body{position:relative;background:var(--light);font-family:"Roboto",Arial,sans-serif;color:var(--ink)}
.abs{position:absolute}

/* header */
.site-header{left:0;top:0;width:960px;height:98px;background:#f7f7f7;border-bottom:1px solid #ddd}
.brand{left:148px;top:36px;display:flex;align-items:center;gap:7px}
.brand-mark{width:14px;height:14px;background:var(--red)}
.brand-name{font-size:19px;font-weight:500;color:var(--red);letter-spacing:.5px}
.main-nav{left:336px;top:41px;display:flex;align-items:center;font-size:10px;color:#555;text-transform:uppercase}
.main-nav a{color:inherit;text-decoration:none;margin-right:24px;line-height:16px}
.main-nav a.active{background:var(--red);color:var(--white);padding:0 7px;border-radius:2px;margin-right:21px}
.search-btn{left:794px;top:41px;width:16px;height:16px;background:var(--red);border-radius:2px}

/* hero */
.hero{left:0;top:98px;width:960px;height:282px;background:linear-gradient(110deg,#3a1d1d 0%,#8f1d1d 25%,#6b2a22 45%,#3d3a2a 65%,#2a2a2a 100%)}
.hero-title{left:0;top:98px;width:960px;text-align:center;padding-top:96px;color:var(--white);font-size:26px;font-weight:500}
.hero-text{left:210px;top:246px;width:540px;text-align:center;color:var(--white);font-size:13px;line-height:21px}

/* services band */
.service-band{left:0;top:380px;width:960px;height:70px;background:var(--red)}
.service-pointer{left:732px;top:366px;width:0;height:0;border-left:12px solid transparent;border-right:12px solid transparent;border-bottom:14px solid var(--red)}
.service{top:393px;width:120px;text-align:center;color:var(--white);font-size:11px}
.service svg{display:block;margin:0 auto 6px;width:24px;height:24px}

/* news */
.news-section{left:0;top:450px;width:960px;height:352px;background:var(--panel);border-bottom:1px solid var(--rule)}
.section-head{display:flex;justify-content:space-between;align-items:flex-end;border-bottom:2px solid var(--rule);padding-bottom:7px}
.section-title{font-size:13px;font-weight:500;color:var(--ink)}
.view-all{font-size:9.5px;color:var(--muted)}
.news-head{left:148px;top:489px;width:662px}
.news-card{top:532px;width:155px;height:226px;background:#f4f4f4;border:1px solid #d6d6d6}
.news-photo{height:85px}
.news-card h3{font-size:12px;font-weight:500;margin:13px 0 0 8px}
.news-card p{font-size:9.5px;line-height:12.6px;color:var(--muted);margin:10px 8px 0 8px}
.news-card a{display:block;font-size:9.5px;color:var(--red);text-decoration:none;font-weight:500;margin:16px 0 0 8px}

/* events + testimonials */
.events-head{left:148px;top:842px;width:326px}
.clients-head{left:486px;top:842px;width:324px}
.slider-arrows{display:flex;gap:2px}
.slider-arrows span{width:12px;height:12px;background:#c4c4c4;border-radius:2px;display:block}
.event{left:149px;width:325px;height:50px}
.event-date{position:absolute;left:0;top:0;width:43px;height:49px;background:#e2e2e2;text-align:center;color:var(--muted);font-size:9px;line-height:11px;padding-top:6px}
.event-date b{display:block;font-size:13px;color:var(--ink);font-weight:500;line-height:16px}
.event h4{position:absolute;left:56px;top:-2px;font-size:12.5px;font-weight:500}
.event p{position:absolute;left:56px;top:22px;font-size:9.5px;line-height:14px;color:#666;width:272px}
.quote{left:486px;top:884px;width:324px;height:113px;background:#e6e6e6;padding:9px 8px;font-size:9.5px;line-height:14px;color:#666}
.quote-pointer{left:530px;top:997px;border-left:10px solid transparent;border-right:10px solid transparent;border-top:10px solid #e6e6e6;width:0;height:0}
.avatar{left:514px;top:1022px;width:52px;height:51px;background:linear-gradient(160deg,#6d6d6d,#2e2e2e)}
.author{left:579px;top:1041px;font-size:9.5px;color:#666}
.author b{color:var(--ink);font-weight:500}

/* footer */
.site-footer{left:0;top:1114px;width:960px;height:86px;background:var(--footer)}
.copyright{left:148px;top:1150px;font-size:9.5px;color:var(--white)}
.social{top:1147px;width:18px;height:18px;border-radius:50%;background:#eee}
</style>
</head>
<body>

<header class="abs site-header"></header>
<div class="abs brand"><span class="brand-mark"></span><span class="brand-name">Quelbrant</span></div>
<nav class="abs main-nav">
  <a class="active" href="#">Home</a>
  <a href="#">Business Unit</a>
  <a href="#">Services</a>
  <a href="#">About Us</a>
  <a href="#">Locations</a>
  <a href="#">Contact Us</a>
</nav>
<div class="abs search-btn">
  <svg width="16" height="16" viewBox="0 0 16 16"><circle cx="7" cy="7" r="3.4" fill="none" stroke="#fff" stroke-width="1.6"/><line x1="9.5" y1="9.5" x2="12.5" y2="12.5" stroke="#fff" stroke-width="1.8"/></svg>
</div>

<section class="abs hero" role="img" aria-label="Blurred photo of red network cables plugged into server equipment"></section>
<h1 class="abs hero-title">MAINTENANCE</h1>
<p class="abs hero-text">Lorem ipsum dolor sit amet, consectetur adipisicing elit,sed do eiusmodtempor incididunt ut labore et dolore magna aliqua.</p>

<div class="abs service-pointer"></div>
<div class="abs service-band"></div>
<div class="abs service" style="left:154px">
  <svg viewBox="0 0 24 24"><circle cx="12" cy="8" r="5" fill="#fff"/><path d="M3 22c0-5 4-8 9-8s9 3 9 8z" fill="#fff"/></svg>Consulting</div>
<div class="abs service" style="left:287px">
  <svg viewBox="0 0 24 24"><circle cx="12" cy="12" r="7.5" fill="none" stroke="#fff" stroke-width="4" stroke-dasharray="3 2.9"/><circle cx="12" cy="12" r="6" fill="none" stroke="#fff" stroke-width="3"/></svg>Engineering</div>
<div class="abs service" style="left:420px">
  <svg viewBox="0 0 24 24"><line x1="4" y1="20" x2="18" y2="6" stroke="#fff" stroke-width="3"/><line x1="5" y1="5" x2="20" y2="20" stroke="#fff" stroke-width="3"/><rect x="14" y="2" width="8" height="5" fill="#fff" transform="rotate(45 18 4)"/></svg>Construction</div>
<div class="abs service" style="left:552px">
  <svg viewBox="0 0 24 24"><circle cx="12" cy="12" r="8" fill="none" stroke="#fff" stroke-width="2.5" stroke-dasharray="9 3.6"/><circle cx="12" cy="4" r="2" fill="#fff"/><circle cx="5" cy="16" r="2" fill="#fff"/><circle cx="19" cy="16" r="2" fill="#fff"/></svg>Operations</div>
<div class="abs service" style="left:684px">
  <svg viewBox="0 0 24 24"><rect x="3" y="2" width="18" height="6" rx="1" fill="#fff"/><rect x="3" y="9" width="18" height="6" fill="#fff"/><rect x="3" y="16" width="18" height="6" rx="1" fill="#fff"/><line x1="6" y1="12" x2="12" y2="12" stroke="#d6202a"/><line x1="6" y1="19" x2="12" y2="19" stroke="#d6202a"/></svg>Maintenance</div>

<section class="abs news-section"></section>
<div class="abs section-head news-head"><h2 class="section-title">Latest News</h2><span class="view-all">View all</span></div>

<article class="abs news-card" style="left:149px">
  <div class="news-photo" role="img" aria-label="Black and white portrait photo of a businessman" style="background:linear-gradient(90deg,#e8e8e8,#9a9a9a)"></div>
  <h3>Lorem Ipsum</h3>
  <p>Lorem ipsum dolor sit amet, consectetur adipiscing elit, sed do eiusmod tempor incidi-dunt ut labore et dolore magna aliqua.</p>
  <a href="#">Read more</a>
</article>
<article class="abs news-card" style="left:318px">
  <div class="news-photo" role="img" aria-label="Photo of a presenter speaking to a seated audience" style="background:linear-gradient(90deg,#cfd6dc,#a9b4bd 60%,#b9a46a)"></div>
  <h3>Lorem Ipsum</h3>
  <p>Lorem ipsum dolor sit amet, consectetur adipiscing elit, sed do eiusmod tempor incidi-dunt ut labore et dolore magna aliqua.</p>
  <a href="#">Read more</a>
</article>
<article class="abs news-card" style="left:487px">
  <div class="news-photo" role="img" aria-label="Photo of colleagues talking at a meeting table" style="background:linear-gradient(90deg,#d9c9a6,#e8e4dc 50%,#9fb4c8)"></div>
  <h3>Lorem Ipsum</h3>
  <p>Lorem ipsum dolor sit amet, consectetur adipiscing elit, sed do eiusmod tempor incidi-dunt ut labore et dolore magna aliqua.</p>
  <a href="#">Read more</a>
</article>
<article class="abs news-card" style="left:656px">
  <div class="news-photo" role="img" aria-label="Photo of business people applauding" style="background:linear-gradient(90deg,#2c2c2c,#7a6152 50%,#b08a70)"></div>
  <h3>Lorem Ipsum</h3>
  <p>Lorem ipsum dolor sit amet, consectetur adipiscing elit, sed do eiusmod tempor incidi-dunt ut labore et dolore magna aliqua.</p>
  <a href="#">Read more</a>
</article>

<div class="abs section-head events-head"><h2 class="section-title">Event Updates</h2><span class="view-all">View all</span></div>
<div class="abs section-head clients-head"><h2 class="section-title">What Clients Say</h2><span class="slider-arrows"><span></span><span></span></span></div>

<div class="abs event" style="top:884px">
  <div class="event-date"><b>17</b>MAY<br>2014</div>
  <h4>Lorem Ipsum</h4>
  <p>Lorem ipsum dolor sit amet, consectetur adipiscing elit. Nulla vehicula feugiat blandit. Nulla facilisi. Nulla tellus nisi...</p>
</div>
<div class="abs event" style="top:954px">
  <div class="event-date"><b>04</b>MAY<br>2014</div>
  <h4>Lorem Ipsum</h4>
  <p>Lorem ipsum dolor sit amet, consectetur adipiscing elit. Nulla vehicula feugiat blandit. Nulla facilisi. Nulla tellus nisi...</p>
</div>
<div class="abs event" style="top:1024px">
  <div class="event-date"><b>23</b>APRIL<br>2014</div>
  <h4>Lorem Ipsum</h4>
  <p>Lorem ipsum dolor sit amet, consectetur adipiscing elit. Nulla vehicula feugiat blandit. Nulla facilisi. Nulla tellus nisi...</p>
</div>

<blockquote class="abs quote">Fusce ele mentum, nulla vel pellentesque consequat, ante nulla hen-drerit arcu, ac tincidunt mauris lacus sed leo. vamus suscipit molestie vestibulum.Fusce elementum, nulla vel pellentesque consequat, ante nulla hendrerit arcu, ac tincidunt mauris lacus sed leo. vamus suscipit molestie vestibulum.Fusce elementum, nulla vel pellentesque conse-quat, ante nulla hendrerit arcu, ac tincidunt mauris lacus sed leo. vamus suscipit molestie vestibulum.</blockquote>
<div class="abs quote-pointer"></div>
<div class="abs avatar" role="img" aria-label="Portrait photo of the quoted client"></div>
<p class="abs author"><b>John Doe</b> - CEO Quelbrant</p>

<footer class="abs site-footer"></footer>
<p class="abs copyright">Quelbrant © 2014, All Rights Reserved</p>
<span class="abs social" style="left:745px" aria-label="Social link"></span>
<span class="abs social" style="left:769px" aria-label="Social link"></span>
<span class="abs social" style="left:793px" aria-label="Social link"></span>

</body>
</html>
```